Plate of the Raven: Half-Page Magazine Ad

advertisement in a travel magazine for a casual/fine dining restaurant in the heart of Whitehorse, Yukon
Needs to say that it is located in the Stonefield Hotel, 247 Larch Avenue.

Northern inspired cuisine
plateoftheraven.example

Don't need to use all the pictures

Dimensions: ad is a half-page, dimensions are 7.25" x 4.8".

Target Market(s)

Upscale dining, corporate travellers

Industry/Entity Type

Restaurant

Colors
0054AA
0677BA
7BADD7
CADEEF
E8F1F8
0094D4
00A9DD
6FCCEA
C7EBF8
E9F6FB
00AB8E
00BBA5
67D7C9
C6EFE9
E9F9F6

Requirements
Must have
• Restaurant logo
Nice to have
• Simple, clean design with upscale feel

```html
<!DOCTYPE html>
<html lang="en">
<head>
<meta charset="utf-8">
<title>Plate of the Raven – Magazine Ad</title>
<link rel="stylesheet" href="https://fonts.googleapis.com/css2?family=Montserrat:wght@400;500;600;700&family=Cormorant+Garamond:wght@600&display=swap">
<style>
  :root {
    --stage: #b4b4b4;
    --paper: #ffffff;
    --ink: #1c1c1c;
    --band: #231f20;
    --frame: #222222;
    --muted: #444444;
  }
  * { box-sizing: border-box; margin: 0; padding: 0; }
  html, body {
    width: 1200px; height: 2298px; overflow: hidden;
    background: var(--stage);
    font-family: "Montserrat", Arial, sans-serif;
    color: var(--ink);
  }
  .ad {
    position: absolute; left: 61px; top: 387px;
    width: 1077px; height: 1523px;
    background: var(--paper);
    box-shadow: 0 6px 14px rgba(0,0,0,.35);
  }
  .gallery {
    position: absolute; left: 44px; top: 46px;
    width: 990px; height: 896px;
    border: 3px solid var(--frame);
    background: var(--frame);
    display: grid;
    grid-template-columns: 294px 396px 1fr;
    grid-template-rows: 333px 1fr;
    gap: 3px;
  }
  .photo { width: 100%; height: 100%; }
  .photo--board { background: linear-gradient(135deg, #5a4b3a, #c89a5a 45%, #e8d28a 60%, #3e4a2a); }
  .photo--soup  { background: linear-gradient(160deg, #d9825f, #e2b04a 40%, #7a8a3a 70%, #b24a3a); }
  .photo--pasta {
    grid-column: 1 / 4;
    background: radial-gradient(ellipse at 45% 50%, #d66a2a 0%, #c0562a 30%, #8a6a4a 55%, #6d8fb8 80%, #9ec2e6 100%);
  }
  .brand-cell {
    background: var(--paper);
    display: flex; align-items: center; justify-content: center; gap: 18px;
  }
  .brand-cell__mark { flex: none; width: 22px; height: 22px; background: var(--ink); }
  .brand-cell__name {
    font-family: "Montserrat", Arial, sans-serif;
    font-weight: 600; font-size: 36px; line-height: 1.2;
    color: var(--ink);
  }
  .headline {
    position: absolute; left: 0; right: 0; top: 975px;
    text-align: center;
    font-family: "Cormorant Garamond", Georgia, serif;
    font-weight: 600;
    font-size: 96px; line-height: 1.1; color: var(--ink);
  }
  .intro {
    position: absolute; left: 0; right: 0; top: 1108px;
    text-align: center; font-size: 27px; line-height: 33px; font-weight: 500;
    color: var(--muted);
  }
  .features {
    position: absolute; left: 0; right: 0; top: 1202px;
    display: flex; justify-content: center;
  }
  .feature {
    display: flex; gap: 16px; width: 400px;
    font-size: 27px; font-weight: 700; line-height: 32px; color: var(--muted);
  }
  .feature:first-child { padding-left: 36px; }
  .feature:last-child { padding-left: 74px; }
  .feature svg { flex: none; margin-top: 6px; }
  .features__divider { width: 2px; height: 76px; background: var(--ink); margin-top: 8px; }
  .location {
    position: absolute; left: 0; right: 0; bottom: 0; height: 181px;
    background: var(--band); color: var(--paper); text-align: center;
  }
  .location__tag {
    position: absolute; left: 366px; top: -28px; width: 350px; height: 54px;
  }
  .location__tag svg { position: absolute; inset: 0; }
  .location__tag span {
    position: relative; display: block; line-height: 54px;
    font-size: 27px; font-weight: 600; color: var(--ink); letter-spacing: .5px;
  }
  .location__address { padding-top: 50px; font-size: 36px; font-weight: 700; }
  .location__url { margin-top: 14px; font-size: 24px; letter-spacing: 5px; font-weight: 400; }
</style>
</head>
<body>
  <article class="ad">
    <section class="gallery">
      <div class="photo photo--board" role="img" aria-label="Charcuterie board with cured meats, cheese, pickles and crackers"></div>
      <div class="brand-cell">
        <span class="brand-cell__mark"></span>
        <span class="brand-cell__name">Plate of<br>the Raven</span>
      </div>
      <div class="photo photo--soup" role="img" aria-label="Lobster with squash soup and a fresh citrus salad"></div>
      <div class="photo photo--pasta" role="img" aria-label="Bowl of pappardelle in rich tomato ragù topped with shaved parmesan and microgreens"></div>
    </section>

    <h1 class="headline">Plate of the Raven</h1>

    <p class="intro">Elegant comfort food that is upscale but simple. Paired with an<br>impressive wine selection and a modern spin on classic cocktails.</p>

    <div class="features">
      <div class="feature">
        <svg width="28" height="28" viewBox="0 0 28 28" aria-hidden="true">
          <circle cx="13" cy="15" r="10" fill="none" stroke="#444" stroke-width="2.5"/>
          <path d="M7 14 L12 20 L25 3" fill="none" stroke="#444" stroke-width="3.5" stroke-linecap="round" stroke-linejoin="round"/>
        </svg>
        <span>Open evenings with<br>a summer patio.</span>
      </div>
      <div class="features__divider"></div>
      <div class="feature">
        <svg width="28" height="28" viewBox="0 0 28 28" aria-hidden="true">
          <circle cx="13" cy="15" r="10" fill="none" stroke="#444" stroke-width="2.5"/>
          <path d="M7 14 L12 20 L25 3" fill="none" stroke="#444" stroke-width="3.5" stroke-linecap="round" stroke-linejoin="round"/>
        </svg>
        <span>Northern inspired<br>cuisine</span>
      </div>
    </div>

    <footer class="location">
      <div class="location__tag">
        <svg width="350" height="54" viewBox="0 0 350 54" aria-hidden="true">
          <polygon points="18,1 349,1 332,53 1,53" fill="#fff" stroke="#231f20" stroke-width="2"/>
        </svg>
        <span>LOCATED IN THE</span>
      </div>
      <p class="location__address">Stonefield Hotel, 247 Larch Avenue.</p>
      <p class="location__url">www.plateoftheraven.example</p>
    </footer>
  </article>
</body>
</html>
```